Alloy wheel repair business needs a website

Install logo previously purchased from makerhive, toolbar with dropdowns. services, gallery, clients , contact ect
Maybe mission statment

Target Market(s)

vehicle owners, auto dealers,insurance companies,

Industry/Entity Type

Alloy Wheel Repair

Coding

Coded - Design and coding required

Number of Pages Required

4 page

Font styles to use
Sans Serif

Colors
0054AA
0677BA
7BADD7
CADEEF
E8F1F8

```html
<!DOCTYPE html>
<html lang="en">
<head>
<meta charset="utf-8">
<title>Rimline Wheelworks</title>
<link href="https://fonts.googleapis.com/css2?family=Audiowide&family=Roboto:wght@400;500;700;900&display=swap" rel="stylesheet">
<style>
:root{
  --blue:#3f82c7;
  --blue-dark:#0054aa;
  --ink:#1d1d1f;
  --dark:#2a2729;
  --grey:#6d6d6d;
  --line:#d8d8d8;
  --white:#fff;
  --star:#f5a623;
}
*{box-sizing:border-box;margin:0;padding:0}
html,body{width:1200px;height:4118px;overflow:hidden}
body{position:relative;background:var(--white);font-family:'Roboto',sans-serif;color:var(--ink)}
.abs{position:absolute}
.display{font-family:'Audiowide',sans-serif;font-weight:400;letter-spacing:1px;text-transform:uppercase}
.btn{position:absolute;display:flex;align-items:center;justify-content:center;gap:8px;background:var(--blue);color:var(--white);border-radius:30px;font-weight:700;font-size:14px;text-transform:uppercase;white-space:nowrap}
.btn .dot{flex:none;width:14px;height:14px;border-radius:50%;background:var(--white);display:inline-flex;align-items:center;justify-content:center}
.btn .dot::after{content:"";border-left:5px solid var(--blue);border-top:3.5px solid transparent;border-bottom:3.5px solid transparent;margin-left:2px}
.photo{position:absolute}
.wave{position:absolute;left:0}

/* header */
.topline{top:0;left:0;width:1200px;height:4px;background:var(--blue)}
.header{top:4px;left:0;width:1200px;height:87px;background:var(--white)}
.brand{position:absolute;display:flex;align-items:center;gap:10px;font-family:'Roboto',sans-serif;font-weight:900;font-size:26px;letter-spacing:2px;text-transform:uppercase}
.brand .mark{width:22px;height:22px;border-radius:50%;background:currentColor}
.header .brand{left:145px;top:28px;color:var(--blue)}
.nav{position:absolute;left:398px;top:37px;display:flex;gap:22px;font-size:14px;font-weight:500;text-transform:uppercase}
.nav .active{color:var(--blue)}
.quote{left:920px;top:29px;width:133px;height:36px;text-transform:none;font-size:14px}

/* hero */
.hero{top:91px;left:0;width:1200px;height:681px;overflow:hidden;background:linear-gradient(100deg,#2d3640 0%,#4a5562 40%,#8a6a3a 70%,#c9811e 100%)}
.hero h1{position:absolute;left:145px;top:190px;font-size:32px;color:var(--white)}
.hero p{position:absolute;left:143px;top:237px;width:440px;font-size:15px;line-height:26px;color:var(--white)}
.hero .btn{left:145px;top:313px;width:170px;height:38px;font-size:15px}
.hero .wave{bottom:0}

/* mission */
.mission-ring{left:174px;top:848px;width:372px;height:372px;border-radius:50%;background:var(--blue)}
.mission-photo{left:190px;top:848px;width:364px;height:364px;border-radius:50%;background:linear-gradient(140deg,#5a5f66,#a9aeb3 55%,#d0d2d4)}
.mission h2{position:absolute;left:635px;top:872px;font-size:36px}
.mission p{position:absolute;left:633px;width:420px;font-size:13px;line-height:22.5px;color:var(--grey);text-align:justify}
.mission .btn{left:635px;top:1138px;width:156px;height:42px}

/* services */
.services{top:1290px;left:0;width:1200px;height:840px;background:linear-gradient(180deg,#2f2b2d,#3a3639 50%,#2a2729)}
.services h2{position:absolute;left:0;width:1200px;top:110px;text-align:center;font-size:36px;color:var(--white)}
.svc{position:absolute;width:441px;height:189px;background:var(--white);border-radius:95px}
.svc .pic{position:absolute;left:18px;top:24px;width:141px;height:141px;border-radius:50%;background:linear-gradient(135deg,#2b2b2b,#8f9499 60%,#c6c8ca)}
.svc h3{position:absolute;left:174px;top:25px;font-size:17px;font-weight:500}
.svc p{position:absolute;left:174px;top:56px;width:240px;font-size:12.5px;line-height:19px;color:var(--grey)}
.svc .btn{left:174px;top:129px;width:126px;height:36px;font-size:12px}
.services .all{left:488px;top:676px;width:227px;height:52px;font-size:15px}

/* reviews */
.reviews h2{position:absolute;left:0;width:1200px;top:2192px;text-align:center;font-size:36px}
.review{position:absolute;width:382px;height:216px;background:var(--white);border-radius:26px;box-shadow:0 3px 10px rgba(0,0,0,.22)}
.review .q{position:absolute;left:88px;top:16px;font-family:Georgia,serif;font-size:60px;line-height:1;color:var(--blue);font-weight:700}
.review p{position:absolute;left:88px;top:60px;width:270px;font-size:12.5px;line-height:22px;color:var(--grey);text-align:justify}
.review h4{position:absolute;left:88px;top:152px;font-size:15px;font-weight:500}
.review .stars{position:absolute;left:88px;top:176px;color:var(--star);font-size:16px;letter-spacing:1px}
.avatar{position:absolute;width:108px;height:108px;border-radius:50%;background:linear-gradient(135deg,#3c3f44,#c26a2a)}
.arrow{position:absolute;top:2368px}

/* contact */
.contact{top:2572px;left:0;width:1200px;height:428px;background:var(--blue)}
.contact .wave{top:0}
.contact h2{position:absolute;left:624px;top:60px;font-size:36px;color:var(--white)}
.contact p{position:absolute;left:625px;top:110px;width:430px;font-size:13px;line-height:22.5px;color:var(--white)}
.field{position:absolute;width:209px;height:37px;background:var(--white);border:1px solid #cfdbe8;font-size:11px;color:#777;padding:12px 12px}
.contact .btn{left:624px;top:319px;width:122px;height:41px;gap:6px;background:var(--white);color:var(--blue);font-size:12px}
.contact .btn .dot{background:var(--blue)}
.contact .btn .dot::after{border-left-color:var(--white)}

/* gallery */
.gallery h2{position:absolute;left:0;width:1200px;top:3068px;text-align:center;font-size:36px}
.gpic{position:absolute}

/* footer */
.footer{top:3720px;left:0;width:1200px;height:398px;background:var(--dark)}
.footer .wave{top:0}
.footer .brand{left:145px;top:155px;color:var(--white)}
.socials{position:absolute;left:165px;top:224px;display:flex;gap:6px}
.socials span{width:34px;height:34px;border-radius:50%;background:var(--white);display:block}
.socials span.on{background:var(--blue)}
.fcol{position:absolute;color:var(--white)}
.fcol h5{font-size:16px;font-weight:700;text-transform:uppercase;margin-bottom:12px;white-space:nowrap}
.fcol li{list-style:none;font-size:13px;height:30.5px;display:flex;align-items:center;gap:10px;white-space:nowrap}
.fcol li::before{content:"»";color:var(--blue);font-weight:700}
.fcol.contactinfo li{gap:12px;height:34px}
.fcol.contactinfo li::before{content:none}
.fcol.contactinfo .ico{flex:none;width:14px;display:flex;justify-content:center}
.rule{position:absolute;left:140px;top:338px;width:920px;height:1px;background:#6a6668}
.copy{position:absolute;left:0;width:1200px;top:352px;text-align:center;font-size:12px;color:var(--white)}
.chat{position:absolute;left:1066px;top:275px;width:34px;height:34px;border-radius:50%;background:var(--blue)}
</style>
</head>
<body>

<div class="abs topline"></div>
<header class="abs header">
  <div class="brand"><span class="mark"></span>Rimline</div>
  <nav class="nav">
    <span class="active">Home</span><span>About Us</span><span>Services</span><span>Gallery</span><span>Clients</span><span>Contact</span>
  </nav>
  <div class="btn quote">Get A Quote</div>
</header>

<section class="abs hero">
  <div class="photo" role="img" aria-label="Orange SUV parked on a hilltop overlooking a city at dusk" style="inset:0"></div>
  <h1 class="display">Rimline Wheelworks</h1>
  <p>Lorem ipsum dolor sit amet, consectetur adipiscing elit, sed do eiusmod tempor incididunt ut aliqua.</p>
  <div class="btn">Get Started <span class="dot"></span></div>
  <svg class="wave" width="1200" height="180" viewBox="0 0 1200 180">
    <path d="M0,23 Q600,257 1200,23 V180 H0 Z" fill="#3f82c7"/>
    <path d="M0,60 Q600,300 1200,60 V180 H0 Z" fill="#fff"/>
  </svg>
</section>

<section class="mission">
  <div class="abs mission-ring"></div>
  <div class="photo mission-photo" role="img" aria-label="Two mechanics inspecting a car engine in a workshop"></div>
  <h2 class="display">Our Mission</h2>
  <p style="top:937px">Lorem ipsum dolor sit amet, consectetur adipiscing elit, sed do eiusmod tempor incididunt ut labore et dolore magna aliqua. Ut enim ad minim veniam, quis nostrud exercitation ullamco laboris nisi ut aliquip ex ea commodo consequat.</p>
  <p style="top:1038px">Sed ut perspiciatis unde omnis iste natus error sit voluptatem accusantium doloremque laudantium, totam rem aperiam, eaque ipsa architecto beatae vitae dicta sunt explicabo.</p>
  <div class="btn">Read More <span class="dot"></span></div>
</section>

<section class="abs services">
  <div class="photo" role="img" aria-label="Dark close-up of a car wheel" style="inset:0;opacity:.25;background:radial-gradient(circle at 55% 45%,#777,transparent 60%)"></div>
  <svg class="wave" width="1200" height="200" viewBox="0 0 1200 200" style="top:0">
    <path d="M0,0 H1200 V170 Q600,-170 0,170 Z" fill="#fff"/>
    <path d="M0,170 Q600,-170 1200,170 L1200,195 Q600,-90 0,195 Z" fill="#3f82c7"/>
  </svg>
  <svg class="wave" width="1200" height="200" viewBox="0 0 1200 200" style="top:640px">
    <path d="M0,20 Q600,340 1200,20 V200 H0 Z" fill="#3f82c7"/>
    <path d="M0,40 Q600,360 1200,40 V200 H0 Z" fill="#fff"/>
  </svg>
  <h2 class="display">Our Services</h2>

  <div class="svc" style="left:145px;top:207px">
    <div class="pic" role="img" aria-label="Technician fitting an alloy wheel"></div>
    <h3>Lorem ipsum dolor</h3>
    <p>Sed ut perspiciatis unde omnis iste error sit voluptatem accusantium sit accusantium doloremque laudantium.</p>
    <div class="btn">Learn More <span class="dot"></span></div>
  </div>
  <div class="svc" style="left:613px;top:207px">
    <div class="pic" role="img" aria-label="Brake disc and caliper close-up"></div>
    <h3>Lorem ipsum dolor</h3>
    <p>Sed ut perspiciatis unde omnis iste error sit voluptatem accusantium sit accusantium doloremque laudantium.</p>
    <div class="btn">Learn More <span class="dot"></span></div>
  </div>
  <div class="svc" style="left:145px;top:432px">
    <div class="pic" role="img" aria-label="Hands repairing an alloy rim"></div>
    <h3>Lorem ipsum dolor</h3>
    <p>Sed ut perspiciatis unde omnis iste error sit voluptatem accusantium sit accusantium doloremque laudantium.</p>
    <div class="btn">Learn More <span class="dot"></span></div>
  </div>
  <div class="svc" style="left:613px;top:432px">
    <div class="pic" role="img" aria-label="Spray painting a dark wheel rim"></div>
    <h3>Lorem ipsum dolor</h3>
    <p>Sed ut perspiciatis unde omnis iste error sit voluptatem accusantium sit accusantium doloremque laudantium.</p>
    <div class="btn">Learn More <span class="dot"></span></div>
  </div>
  <div class="btn all">View All Services <span class="dot"></span></div>
</section>

<section class="reviews">
  <h2 class="display">Customer Reviews</h2>
  <svg class="arrow" style="left:76px" width="24" height="36" viewBox="0 0 24 36"><path d="M18,4 L6,18 L18,32" stroke="#1d1d1f" stroke-width="4" fill="none"/></svg>
  <svg class="arrow" style="left:1100px" width="24" height="36" viewBox="0 0 24 36"><path d="M6,4 L18,18 L6,32" stroke="#1d1d1f" stroke-width="4" fill="none"/></svg>

  <div class="review" style="left:195px;top:2278px">
    <div class="q">&#8220;</div>
    <p>Lorem ipsum dolor sit amet, consectetur adipiscing elit, sed do eiusmod tempor incididunt ut labore et dolore magna aliqua. Ut enim ad minim veniam.</p>
    <h4>Jordan</h4>
    <div class="stars">★★★★★</div>
  </div>
  <div class="avatar" role="img" aria-label="Customer portrait" style="left:147px;top:2332px"></div>

  <div class="review" style="left:672px;top:2278px">
    <div class="q">&#8220;</div>
    <p>Lorem ipsum dolor sit amet, consectetur adipiscing elit, sed do eiusmod tempor incididunt ut labore et dolore magna aliqua. Ut enim ad minim veniam.</p>
    <h4>Morgan</h4>
    <div class="stars">★★★★★</div>
  </div>
  <div class="avatar" role="img" aria-label="Customer portrait" style="left:624px;top:2332px"></div>
</section>

<section class="abs contact">
  <svg class="wave" width="600" height="428" viewBox="0 0 600 428">
    <path d="M0,0 H516 Q600,214 508,428 H0 Z" fill="#fff"/>
    <path d="M0,0 H500 Q580,214 490,428 H0 Z" fill="#2f3338"/>
  </svg>
  <div class="photo" role="img" aria-label="Mechanic mounting an alloy wheel on a car" style="left:0;top:0;width:560px;height:428px;clip-path:path('M0,0 H500 Q580,214 490,428 H0 Z');background:linear-gradient(120deg,#1e2226,#5c636b 45%,#2b3036)"></div>
  <h2 class="display">Contact Us</h2>
  <p>Lorem ipsum dolor sit amet, consectetur adipiscing elit, sed do eiusmod tempor incididunt ut labore et dolore magna aliqua. Ut enim ad minim veniam, quis nostrud exercitation ullamco laboris.</p>
  <div class="field" style="left:626px;top:203px">Your Name</div>
  <div class="field" style="left:847px;top:203px">Email Address</div>
  <div class="field" style="left:626px;top:252px">Your Phone Number</div>
  <div class="field" style="left:847px;top:252px">Location</div>
  <div class="btn">Send Message <span class="dot"></span></div>
</section>

<section class="gallery">
  <h2 class="display">Our Gallery</h2>
  <div class="gpic" role="img" aria-label="Tyre being fitted on a changing machine" style="left:150px;top:3161px;width:444px;height:216px;background:linear-gradient(120deg,#5b5e62,#b9bcbf 50%,#c4392b)"></div>
  <div class="gpic" role="img" aria-label="Mechanic cleaning a car wheel" style="left:606px;top:3161px;width:217px;height:236px;background:linear-gradient(135deg,#d9dcdf,#8a9096 60%,#3a3d42)"></div>
  <div class="gpic" role="img" aria-label="Gloved hand polishing a car panel" style="left:833px;top:3161px;width:218px;height:236px;background:linear-gradient(135deg,#7a7f86,#c7c9cc 50%,#b23a3a)"></div>
  <div class="gpic" role="img" aria-label="Silver alloy wheel being serviced" style="left:150px;top:3386px;width:217px;height:240px;background:linear-gradient(135deg,#2e3034,#a6abb0 55%,#d9c8a8)"></div>
  <div class="gpic" role="img" aria-label="Bronze alloy wheel close-up" style="left:377px;top:3386px;width:217px;height:240px;background:linear-gradient(135deg,#1f2124,#8a5a2e 55%,#3a3c40)"></div>
  <div class="gpic" role="img" aria-label="Technician cleaning a car wheel" style="left:606px;top:3409px;width:445px;height:217px;background:linear-gradient(110deg,#2a2c30,#6e7379 45%,#b52b2b 60%,#8a8f95)"></div>
</section>

<footer class="abs footer">
  <svg class="wave" width="1200" height="160" viewBox="0 0 1200 160">
    <path d="M0,0 H1200 V150 Q600,-130 0,150 Z" fill="#fff"/>
    <path d="M0,150 Q600,-130 1200,150 L1200,168 Q600,-104 0,168 Z" fill="#3f82c7"/>
  </svg>
  <div class="brand"><span class="mark"></span>Rimline</div>
  <div class="socials"><span></span><span></span><span class="on"></span><span></span></div>

  <div class="fcol" style="left:413px;top:108px">
    <h5>Quick Links</h5>
    <ul><li>Home</li><li>About us</li><li>Services</li><li>Gallery</li><li>Clients</li><li>Contact</li></ul>
  </div>
  <div class="fcol" style="left:605px;top:108px">
    <h5>Important</h5>
    <ul><li>Terms of Use</li><li>Site Map</li><li>Privacy Policy</li><li>Disclaimer</li></ul>
  </div>
  <div class="fcol contactinfo" style="left:795px;top:108px">
    <h5>Contact Us</h5>
    <ul>
      <li><span class="ico"><svg width="12" height="14" viewBox="0 0 12 14"><path d="M6,0 A5,5 0 0 1 11,5 C11,9 6,14 6,14 C6,14 1,9 1,5 A5,5 0 0 1 6,0 Z" fill="#fff"/><circle cx="6" cy="5" r="2" fill="#2a2729"/></svg></span>742 Orchard Lane Fairview PA 17000</li>
      <li><span class="ico"><svg width="12" height="14" viewBox="0 0 12 14"><rect x="2" y="0" width="8" height="14" rx="1.5" fill="#fff"/><rect x="3.5" y="2" width="5" height="8" fill="#2a2729"/></svg></span>555-210-4821</li>
      <li><span class="ico"><svg width="12" height="14" viewBox="0 0 12 14"><rect x="0" y="4" width="12" height="9" rx="1" fill="#fff"/><rect x="3" y="0" width="6" height="5" fill="#fff"/></svg></span>+1 555-014-2290</li>
      <li><span class="ico"><svg width="14" height="12" viewBox="0 0 14 12"><rect x="1" y="1" width="12" height="10" fill="none" stroke="#fff" stroke-width="1.5"/><path d="M1,1 L7,7 L13,1" fill="none" stroke="#fff" stroke-width="1.5"/></svg></span>hello@rimlinewheels.com</li>
    </ul>
  </div>
  <div class="chat"></div>
  <div class="rule"></div>
  <div class="copy">© 2023 &nbsp;Rimline Wheelworks &nbsp;| &nbsp;All Rights Reserved</div>
</footer>

</body>
</html>
```